Silver Kite Venture Series Travel Brochure

I'm looking for a brochure design for a new travel product - Silver Kite Venture Series, catering for students above 12 years old. Target audience are schools that do destination projects. Brochure to be read by head teacher, parents and students.

Brochure should be A4 in size, 4-6 pages. Format of brochure is hard cover (a folder) with inlet for flyers. Flyers for destinations will be updated from time to time.

Finished job needs to be converted to electronic format for website and email proposal usage.

Attached is text to be used on brochure. Order of section can be adjusted.

For "Elements of the trip", please understand the contents and explain/display it in a graphic form.

For flyer, please come out with a template that I can use for other destinations. The main elements - what's included, number of days, location for pictures, itinerary, educational focus, should be alterable. Attached are text for two sample destinations.
Also attached (tour itinerary example) a version of flyer that I like.

I'm attaching some pictures here. If you find more suitable pictures, please feel free to use them.

Reason: I'm extending the deadline of this project by 4 days, as I need to add details & photo of another travel specialist in personnel session (total of 3 members). Also, in view of the amount of work a designer has to do for this project, I'm giving you more time for submission. Please do not hesitate to be in touch should you need more than 4 days extension. Thank you.

Target Market(s)

Schools - especially the head teacher and parents, to send students above 12 years old to travel

Industry/Entity Type

Electronic

Requirements
Must have
• This is a travel brochure with education elements in it. Parents feel better when their children are travelling for a purpose and lead by responsible teachers/adults whom they can trust. So, the design has to emphasis that education elements and safety are our utmost priority.
Nice to have
• We specialise in environmental study. So, it is nice to have the environmental touch in the design.
Should not have
• Our target market segment is the Middle East, which can be quite sensitive to religion. I prefer not to have any religious related illustration on the design.

```html
<!DOCTYPE html>
<html lang="en">
<head>
<meta charset="utf-8">
<title>FAQ – Silver Kite Venture Series</title>
<link rel="stylesheet" href="https://fonts.googleapis.com/css2?family=Alfa+Slab+One&family=Source+Sans+3:ital,wght@0,400;0,700;1,400&display=swap">
<style>
  :root {
    --navy: #134a7e;
    --lime: #9fcc3b;
    --sky: #5ea7da;
    --stem: #3aa447;
    --leaf-light: #a6d86a;
    --leaf-dark: #3f9a3a;
    --title-green: #2f9a3f;
    --ink: #1d1d1b;
    --white: #ffffff;
    --backdrop: #eeeeee;
  }
  * { margin: 0; padding: 0; box-sizing: border-box; }
  html, body { width: 864px; height: 1200px; overflow: hidden; }
  body {
    background: var(--backdrop);
    font-family: "Source Sans 3", Arial, sans-serif;
    color: var(--ink);
    position: relative;
  }
  .page {
    position: absolute; left: 27px; top: 27px; width: 810px; height: 1145px;
    background: var(--white);
    box-shadow: 3px 4px 10px rgba(0,0,0,0.35);
  }
  .faq-title {
    position: absolute; left: 67px; top: 104px;
    font-family: "Alfa Slab One", Georgia, serif;
    font-size: 19px; font-weight: 400; color: var(--title-green); letter-spacing: 0.5px;
  }
  .panel { position: absolute; }
  .parents-label-band { left: 67px; top: 181px; width: 219px; height: 351px; background: var(--navy); }
  .parents-qa-band { left: 286px; top: 181px; width: 513px; height: 351px; background: var(--lime); }
  .teachers-qa-band { left: 67px; top: 583px; width: 514px; height: 425px; background: var(--sky); }
  .teachers-label-band { left: 581px; top: 583px; width: 218px; height: 425px; background: var(--navy); }
  .section-label {
    position: absolute;
    font-family: "Alfa Slab One", Georgia, serif;
    font-size: 29px; font-weight: 400; color: var(--white); letter-spacing: 0.3px; line-height: 1;
  }
  .parents-label { left: 85px; top: 348px; }
  .teachers-label { left: 607px; top: 779px; }
  .sprout { position: absolute; left: 0; top: 0; width: 864px; height: 1200px; pointer-events: none; }
  .qa-list { position: absolute; font-size: 14px; line-height: 16.8px; hyphens: auto; }
  .parents-qa { left: 335px; top: 224px; width: 443px; }
  .teachers-qa { left: 85px; top: 633px; width: 445px; }
  .question { font-weight: 700; color: var(--white); }
  .answer {
    font-style: italic; color: var(--ink);
    padding-left: 10px; text-align: justify;
  }
  .contact {
    position: absolute; left: 79px; top: 1043px;
    font-size: 10.3px; line-height: 14px; color: var(--ink); font-style: normal;
  }
  .contact strong { font-weight: 700; }
</style>
</head>
<body>
  <div class="page"></div>

  <h1 class="faq-title">FAQ</h1>

  <div class="panel parents-label-band"></div>
  <div class="panel parents-qa-band"></div>
  <div class="panel teachers-qa-band"></div>
  <div class="panel teachers-label-band"></div>

  <svg class="sprout" viewBox="0 0 864 1200" xmlns="http://www.w3.org/2000/svg">
    <defs>
      <linearGradient id="leafTone" x1="0" y1="0" x2="1" y2="1">
        <stop offset="0" stop-color="#a6d86a"/>
        <stop offset="1" stop-color="#3f9a3a"/>
      </linearGradient>
    </defs>
    <line x1="286" y1="190" x2="286" y2="545" stroke="#3aa447" stroke-width="4"/>
    <rect x="240" y="148" width="106" height="46" rx="8" fill="url(#leafTone)"
          role="img" aria-label="Green sprout leaves topping the stem"/>
    <line x1="581" y1="596" x2="581" y2="1026" stroke="#3aa447" stroke-width="4"/>
    <rect x="459" y="550" width="178" height="48" rx="8" fill="url(#leafTone)"
          role="img" aria-label="Green sprout leaves topping the stem"/>
  </svg>

  <h2 class="section-label parents-label">PARENTS</h2>
  <h2 class="section-label teachers-label">TEACHERS</h2>

  <dl class="qa-list parents-qa">
    <dt class="question">How do I know I am getting value for money?</dt>
    <dd class="answer">All aspects of the cost for the tours are carefully planned, with comprehensive subject focused.</dd>
    <dt class="question">If my child gets sick or injured on the trip, what arrangements will be made?</dt>
    <dd class="answer">We have comprehensive knowledge of all local services and foreign/overseas supports.</dd>
    <dt class="question">Can I join my children, whether for the whole duration or just part of it?</dt>
    <dd class="answer">Yes, we can normally make these types of arrangement, but only the tours during holiday periods and it is subject to individual school’s choice.</dd>
    <dt class="question">Can my child extend his/her trip?</dt>
    <dd class="answer">Yes, this would only happen furing holiday periods and subject to individual school.</dd>
    <dt class="question">Are vaccinations needed?</dt>
    <dd class="answer">Depends on destination, this will be advised with sufficient time before departure.</dd>
  </dl>

  <dl class="qa-list teachers-qa">
    <dt class="question">Are the guides during the trip fully qualified and first-aid trained?</dt>
    <dd class="answer">Yes.</dd>
    <dt class="question">How much travel time will there be?</dt>
    <dd class="answer">Travel times vary but are kept to the minimum possible to maximise activity time.</dd>
    <dt class="question">How up-to-date are your programmes?</dt>
    <dd class="answer">Programmes are checked and revised frequently.</dd>
    <dt class="question">How safe are the places we stay?</dt>
    <dd class="answer">Safety is our top priority and accommodation is chosen very carefully.</dd>
    <dt class="question">How do I arrange with you a pre-visit to the school?</dt>
    <dd class="answer">If you are interested in our tour, we can arrange a meeting at your school. We will gather your requirements and needs during the meeting and then come out with a suitable programme and costing. Once programme and dates are fixed, we can proceed with booking.</dd>
    <dt class="question">What is the smallest/largest number of students I can bring?</dt>
    <dd class="answer">Ideally, smallest number is 8 students and largest number is not more than 40 students. Our ratio of students to tour director/teacher is 8:1, therefore smallest number is 8 students. We prefer students to have sufficient space to interact in accommodation and transportation that we use.</dd>
  </dl>

  <address class="contact">
    <strong>Harbourline Travel Management</strong><br>
    804 Palm Ridge Offices, Marina Heights,<br>
    PO Box 220417, Dubai, UAE<br>
    <strong>Tel:</strong> +971 4 555 0142<br>
    <strong>Fax:</strong> +971 4 555 0143<br>
    <strong>Email:</strong> info@harbourlinetravel.example
  </address>
</body>
</html>
```